Consumer and commercial IOT solutions (Internet Of Things)

We are a startup and are looking for business cards with logo. The logo will appear on all of our media as well as our ecommerce site and social sites that have yet to be developed. We want to present a fresh face on a high tech company that innovates at every turn. You can read about our solutions on our information only web site www.plonaxhub.net - We have some wording we would like used on our business cards but there is no place for this except for here. The company name is "RM Industrial IOT" I have some samples of logos I am interested in seeing but I will let your team make the initial presentations

```html
<!DOCTYPE html>
<html lang="en">
<head>
<meta charset="UTF-8">
<title>RM Industrial IOT – Business Card</title>
<link href="https://fonts.googleapis.com/css2?family=Montserrat:wght@400;500;700&display=swap" rel="stylesheet">
<style>
  :root {
    --navy: #0d2140;
    --navy-deep: #071a33;
    --navy-light: #1c3656;
    --orange: #f26b1d;
    --white: #ffffff;
    --ink: #1a2640;
    --stage: #e9e7e3;
  }
  * { box-sizing: border-box; margin: 0; padding: 0; }
  html, body {
    width: 1200px; height: 900px; overflow: hidden;
    background: var(--stage);
    font-family: "Montserrat", sans-serif;
  }
  .sheet {
    width: 1200px; height: 900px;
    display: flex; flex-direction: column; align-items: center; justify-content: center;
    gap: 40px;
  }
  .card {
    width: 700px; height: 400px;
    border-radius: 22px;
    position: relative; overflow: hidden;
    box-shadow: 0 10px 28px rgba(0,0,0,0.18);
  }

  /* Front */
  .card--front {
    background: linear-gradient(135deg, var(--navy-deep) 0%, var(--navy) 55%, var(--navy-light) 100%);
    display: flex; align-items: center; justify-content: center; gap: 20px;
  }
  .brand-dot {
    width: 28px; height: 28px; border-radius: 50%;
    background: var(--orange);
  }
  .brand-name {
    color: var(--white);
    font-weight: 500;
    font-size: 34px;
    line-height: 1.2;
    white-space: nowrap;
  }

  /* Back */
  .card--back { background: var(--white); }
  .back-panel {
    position: absolute; inset: 0;
    background: linear-gradient(135deg, var(--navy-deep) 0%, var(--navy) 60%, var(--navy-light) 100%);
    clip-path: polygon(0 0, 42% 0, 52% 100%, 0 100%);
    display: flex; align-items: center;
    padding-left: 44px;
  }
  .back-panel .brand-name { font-size: 24px; }
  .details {
    position: absolute; left: 410px; top: 92px; width: 260px;
  }
  .person-name {
    font-weight: 700; font-size: 24px; letter-spacing: 0.5px;
    color: var(--ink); text-transform: uppercase;
  }
  .person-name .surname { color: var(--orange); }
  .person-role {
    font-size: 17px; color: var(--ink); letter-spacing: 1px;
    text-transform: uppercase; margin-top: 4px;
  }
  .rule {
    height: 2px; background: var(--orange); width: 240px;
    margin: 22px 0 20px;
  }
  .contact-list { list-style: none; }
  .contact-list li {
    display: flex; align-items: center; gap: 12px;
    font-size: 17px; color: var(--ink); margin-bottom: 8px;
  }
  .contact-list svg { width: 16px; height: 16px; flex: none; }
</style>
</head>
<body>
<main class="sheet">
  <section class="card card--front">
    <div class="brand-dot"></div>
    <div class="brand-name">RM Industrial IOT</div>
  </section>

  <section class="card card--back">
    <div class="back-panel">
      <div class="brand-name">RM Industrial IOT</div>
    </div>
    <div class="details">
      <p class="person-name">Marcus <span class="surname">Delaney</span></p>
      <p class="person-role">Co-Founder &amp; CEO</p>
      <div class="rule"></div>
      <ul class="contact-list">
        <li>
          <svg viewBox="0 0 24 24" aria-hidden="true"><path fill="#f26b1d" d="M6.6 10.8a15.1 15.1 0 0 0 6.6 6.6l2.2-2.2c.3-.3.7-.4 1-.2 1.1.4 2.3.6 3.6.6.6 0 1 .4 1 1V20c0 .6-.4 1-1 1A17 17 0 0 1 3 4c0-.6.4-1 1-1h3.5c.6 0 1 .4 1 1 0 1.3.2 2.5.6 3.6.1.3 0 .7-.2 1z"/></svg>
          0471205839
        </li>
        <li>
          <svg viewBox="0 0 24 24" aria-hidden="true"><rect x="3" y="5" width="18" height="14" rx="1.5" fill="none" stroke="#f26b1d" stroke-width="2"/><path d="M3.5 6l8.5 7 8.5-7" fill="none" stroke="#f26b1d" stroke-width="2"/></svg>
          info@plonaxhub.com
        </li>
        <li>
          <svg viewBox="0 0 24 24" aria-hidden="true"><circle cx="12" cy="12" r="9" fill="none" stroke="#f26b1d" stroke-width="2"/><path d="M3 12h18M12 3c3 3 3 15 0 18M12 3c-3 3-3 15 0 18" fill="none" stroke="#f26b1d" stroke-width="1.6"/></svg>
          www.plonaxhub.net
        </li>
      </ul>
    </div>
  </section>
</main>
</body>
</html>
```